Brimsett Gardening Fresh New Website

We are looking to create a simple fresh website for our landscaping business. The website should appeal to a 'high end' audience. We deal with a lot of Embassies and affluent clients who have extremely large gardens that are meticulously maintained. The site is about communicating our excellent landscaping and customer service skills and encouraging new clients to reach out and engage us to take care of their gardens.

The website is basically going to be our business card, it will have almost no functionality other than two 'contact us' forms, one for smaller clients and one for more detailed projects.

The website will not have a lot of written content and will have to show photos of beautifully landscaped gardens.

The main logo in black will influence the site, however, we are open to all suggestions.

We are expecting to have the following pages:
Home Page
Services
About Us
Contact Us
Showcase (photo gallery of our work)

We need someone who can code it to wordpress and be available for minor changes over a number of days. They will be simple tweaks.

```html
<!DOCTYPE html>
<html lang="en">
<head>
<meta charset="utf-8">
<title>Brimsett Gardening</title>
<link href="https://fonts.googleapis.com/css2?family=Merriweather:wght@400;700&family=Open+Sans:wght@400;600&display=swap" rel="stylesheet">
<style>
:root{
  --gold:#c9962b;
  --gold-light:#e2b547;
  --gold-dark:#a8761c;
  --ink:#1b1b1b;
  --dark:#1a1a1a;
  --cream:#fcf5ec;
  --beige:#ebe1d3;
  --text:#2a2a2a;
  --muted:#666;
  --white:#fff;
  --line:#d9d9d9;
}
*{margin:0;padding:0;box-sizing:border-box}
html,body{width:1200px;height:4153px;overflow:hidden}
body{position:relative;background:var(--white);font-family:"Open Sans",sans-serif;color:var(--text)}
.abs{position:absolute}
.serif{font-family:"Merriweather",serif}
.btn-gold{background:linear-gradient(180deg,var(--gold-light),var(--gold-dark));color:var(--white);font-family:"Merriweather",serif;font-weight:700;display:flex;align-items:center;justify-content:center}

/* header */
.topline{left:0;top:0;width:1200px;height:5px;background:var(--gold-light)}
.header{left:0;top:5px;width:1200px;height:85px;background:var(--dark)}
.logo-tab{left:100px;top:5px;width:140px;height:121px;background:var(--dark);border-radius:0 0 10px 10px;z-index:3;display:flex;flex-direction:column;align-items:center;justify-content:center;gap:8px}
.logo-dot{width:26px;height:26px;border-radius:50%;border:2px solid var(--gold)}
.logo-name{font-family:"Merriweather",serif;color:var(--gold);font-size:13px;letter-spacing:3px;text-align:center;line-height:1.35}
.nav a{position:absolute;top:37px;font-family:"Merriweather",serif;font-size:15px;font-weight:700;color:var(--white);text-decoration:none;letter-spacing:.3px}
.nav a.active{color:var(--gold-light)}
.nav .nav-cta{left:965px;top:26px;width:137px;height:45px;border-radius:23px;font-size:15px;color:var(--white)}
.search{left:919px;top:38px}

/* hero */
.hero{left:0;top:90px;width:1200px;height:600px;background:linear-gradient(180deg,#4f5a3e 0%,#3f6a2c 40%,#6f8a3a 70%,#5e8f2e 100%)}
.hero h1{position:absolute;left:0;width:1200px;top:235px;text-align:center;font-family:"Merriweather",serif;font-weight:700;color:var(--white);font-size:44px;line-height:70px;letter-spacing:1px;text-shadow:0 2px 8px rgba(0,0,0,.45)}

/* about */
.ring{left:142px;top:842px;width:420px;height:420px;border-radius:50%;background:var(--beige)}
.ring-photo{left:167px;top:867px;width:370px;height:370px;border-radius:50%;background:radial-gradient(circle at 60% 40%,#8fb55a,#4e6b2a 60%,#3a2a1e)}
.square-photo{left:101px;top:797px;width:252px;height:236px;background:linear-gradient(160deg,#e0a35a,#6b6a3a 55%,#3d4a24);border:4px solid var(--white);border-top:none;border-left:none}
.about-title{left:634px;top:822px;font-size:34px;font-weight:700;color:var(--ink)}
.about-text{left:634px;top:878px;width:455px;font-size:14.5px;line-height:31px;color:var(--text)}
.about-text p+p{margin-top:31px}
.read-more{left:634px;top:1185px;width:138px;height:46px;border-radius:23px;font-size:15px}

/* services */
.services{left:0;top:1363px;width:1200px;height:685px;background:var(--cream)}
.section-title{position:absolute;left:0;width:1200px;text-align:center;font-family:"Merriweather",serif;font-weight:700;color:var(--gold);font-size:32px}
.card{position:absolute;top:150px;width:268px}
.card .photo{width:268px;height:305px}
.card .badge{position:absolute;left:93px;top:265px;width:82px;height:82px;border-radius:50%;background:var(--white);display:flex;align-items:center;justify-content:center}
.card h3{margin-top:52px;text-align:center;font-family:"Merriweather",serif;font-weight:400;font-size:20px;color:var(--ink)}
.card .more{display:flex;align-items:center;justify-content:center;margin:26px auto 0;width:166px;height:48px;border:2px solid var(--gold-light);font-family:"Merriweather",serif;font-size:18px;color:var(--gold)}

/* request */
.request{left:0;top:2052px;width:1200px;height:569px;background:#000}
.request .photo{position:absolute;left:0;top:0;width:900px;height:569px;background:linear-gradient(90deg,#6f8a45 0%,#6d7a4a 40%,#3a3a2a 62%,#000 100%)}
.request h2{position:absolute;left:548px;top:62px;font-family:"Merriweather",serif;font-weight:700;font-size:33px;color:var(--white)}
.field{position:absolute;background:var(--white);border-radius:3px;font-size:13px;color:#444;padding:0 12px;display:flex;align-items:center}
.field.area{align-items:flex-start;padding-top:12px}
.submit-sq{position:absolute;left:548px;top:458px;width:126px;height:38px;border-radius:3px;font-size:14px}

/* gallery */
.g-photo{position:absolute;top:2781px;width:232px;height:289px}
.g-follow{border:5px solid var(--gold-light);display:flex;flex-direction:column;align-items:center;justify-content:center;gap:18px;color:var(--white);font-family:"Merriweather",serif;font-size:18px}
.g-view{left:518px;top:3126px;width:164px;height:44px;font-size:18px}

/* contact */
.contact-section{left:0;top:3258px;width:1200px;height:528px;background:var(--cream)}
.c-field{position:absolute;background:var(--white);border-radius:6px;box-shadow:0 2px 8px rgba(0,0,0,.12);font-size:14px;color:#555;padding:0 17px;display:flex;align-items:center}
.c-field.area{align-items:flex-start;padding-top:18px}
.c-submit{left:531px;top:3649px;width:137px;height:51px;border-radius:26px;font-size:18px}

/* footer */
.footer{left:0;top:3786px;width:1200px;height:367px;background:var(--dark);color:var(--white)}
.f-logo{position:absolute;left:96px;top:78px;width:180px;text-align:center}
.f-logo .logo-dot{margin:0 auto 18px;width:40px;height:40px}
.f-logo .logo-name{font-size:20px;letter-spacing:6px;line-height:1.3}
.social{position:absolute;top:224px;width:26px;height:26px;border-radius:50%;background:var(--gold)}
.f-col{position:absolute;top:62px}
.f-col h4{font-family:"Merriweather",serif;font-weight:400;font-size:23px;margin-bottom:8px}
.f-col li{list-style:none;font-size:14.5px;height:31px;display:flex;align-items:center;gap:10px}
.f-contact{position:absolute;left:852px;top:60px}
.f-contact h4{position:absolute;left:64px;top:6px;white-space:nowrap;font-family:"Merriweather",serif;font-weight:400;font-size:23px}
.f-contact p{position:absolute;left:4px;white-space:nowrap;font-size:14.5px}
.divider{position:absolute;left:105px;top:308px;width:990px;height:1px;background:#8a8a8a}
.copyright{position:absolute;left:0;width:1200px;top:323px;text-align:center;font-size:14.5px}
</style>
</head>
<body>

<div class="abs topline"></div>
<header class="abs header">
  <nav class="nav">
    <a class="active" style="left:448px">HOME</a>
    <a style="left:548px">SERVICES</a>
    <a style="left:676px">ABOUT US</a>
    <a style="left:807px">SHOWCASE</a>
    <svg class="abs search" width="20" height="20" viewBox="0 0 20 20" fill="none" stroke="#fff" stroke-width="2"><circle cx="8" cy="8" r="6"/><line x1="12.5" y1="12.5" x2="18" y2="18"/></svg>
    <a class="nav-cta btn-gold">CONTACT US</a>
  </nav>
</header>
<div class="abs logo-tab">
  <div class="logo-dot"></div>
  <div class="logo-name">BRIMSETT<br>GARDENING</div>
</div>

<section class="abs hero" role="img" aria-label="Landscaped park garden with lawn, flowering shrubs and a winding path">
  <h1>WELCOME TO<br>BRIMSETT GARDENING</h1>
</section>

<div class="abs ring"></div>
<div class="abs ring-photo" role="img" aria-label="Gloved hands planting flowers in soil"></div>
<div class="abs square-photo" role="img" aria-label="Gardener tending a rooftop vegetable garden at sunset"></div>
<h2 class="abs serif about-title">ABOUT US</h2>
<div class="abs about-text">
  <p>Lorem ipsum dolor sit amet, consectetur adipiscing elit, sed do eiusmod tempor incididunt ut labore et dolore magna aliqua. Ut enim ad minim veniam, quis nostrud exercitation ullamco laboris nisi ut aliquip ex ea commodo consequat.</p>
  <p>Duis aute irure dolor in reprehenderit in voluptate velit esse cillum dolore eu fugiat nulla pariatur. Excepteur sint occaecat cupidatat non proident, sunt in culpa qui officia deserunt mollit anim id est laborum.</p>
</div>
<div class="abs btn-gold read-more">READ MORE</div>

<section class="abs services">
  <h2 class="section-title" style="top:78px">OUR SERVICES</h2>
  <div class="card" style="left:23px">
    <div class="photo" role="img" aria-label="House front with green lawn and flower beds" style="background:linear-gradient(180deg,#cfc7b5 0%,#7a9a4a 45%,#5ca832 100%)"></div>
    <div class="badge"><svg width="40" height="30" viewBox="0 0 40 30" fill="none" stroke="#c9962b" stroke-width="1.6"><line x1="4" y1="26" x2="36" y2="26"/><line x1="14" y1="26" x2="14" y2="14"/><line x1="26" y1="26" x2="26" y2="14"/><circle cx="14" cy="10" r="5"/><circle cx="26" cy="10" r="5"/></svg></div>
    <h3>Lorem ipsum dolor</h3><div class="more">View More</div>
  </div>
  <div class="card" style="left:318px">
    <div class="photo" role="img" aria-label="Modern pergola with hedges and lawn" style="background:linear-gradient(180deg,#9fb27a 0%,#4a5a3a 45%,#6b9a3a 100%)"></div>
    <div class="badge"><svg width="40" height="30" viewBox="0 0 40 30" fill="none" stroke="#c9962b" stroke-width="1.6"><line x1="4" y1="26" x2="36" y2="26"/><line x1="14" y1="26" x2="14" y2="14"/><line x1="26" y1="26" x2="26" y2="14"/><circle cx="14" cy="10" r="5"/><circle cx="26" cy="10" r="5"/></svg></div>
    <h3>Lorem ipsum dolor</h3><div class="more">View More</div>
  </div>
  <div class="card" style="left:613px">
    <div class="photo" role="img" aria-label="Stepping stone path through lawn with garden lamp" style="background:linear-gradient(180deg,#c8ccc4 0%,#7a8a4a 45%,#6fa030 100%)"></div>
    <div class="badge"><svg width="40" height="30" viewBox="0 0 40 30" fill="none" stroke="#c9962b" stroke-width="1.6"><line x1="4" y1="26" x2="36" y2="26"/><line x1="14" y1="26" x2="14" y2="14"/><line x1="26" y1="26" x2="26" y2="14"/><circle cx="14" cy="10" r="5"/><circle cx="26" cy="10" r="5"/></svg></div>
    <h3>Lorem ipsum dolor</h3><div class="more">View More</div>
  </div>
  <div class="card" style="left:910px">
    <div class="photo" role="img" aria-label="Gravel garden path with pink flowers beside a house" style="background:linear-gradient(180deg,#a8b86a 0%,#8a7a5a 50%,#6a8a3a 100%)"></div>
    <div class="badge"><svg width="40" height="30" viewBox="0 0 40 30" fill="none" stroke="#c9962b" stroke-width="1.6"><line x1="4" y1="26" x2="36" y2="26"/><line x1="14" y1="26" x2="14" y2="14"/><line x1="26" y1="26" x2="26" y2="14"/><circle cx="14" cy="10" r="5"/><circle cx="26" cy="10" r="5"/></svg></div>
    <h3>Lorem ipsum dolor</h3><div class="more">View More</div>
  </div>
</section>

<section class="abs request">
  <div class="photo" role="img" aria-label="Gardener watering a lawn with a hose in front of a log cabin"></div>
  <h2>Request Service or an Estimate</h2>
  <div class="field" style="left:548px;top:150px;width:267px;height:40px">Name</div>
  <div class="field" style="left:832px;top:150px;width:266px;height:40px">Email</div>
  <div class="field" style="left:548px;top:213px;width:267px;height:40px">Phone</div>
  <div class="field" style="left:832px;top:213px;width:266px;height:40px">Address</div>
  <div class="field" style="left:548px;top:274px;width:267px;height:42px">City/Town</div>
  <div class="field" style="left:832px;top:274px;width:266px;height:42px;justify-content:space-between">Service Needed<svg width="9" height="6" viewBox="0 0 9 6"><path d="M0 0h9L4.5 6z" fill="#222"/></svg></div>
  <div class="field area" style="left:548px;top:343px;width:550px;height:87px">Comment</div>
  <div class="btn-gold submit-sq">Submit</div>
</section>

<h2 class="section-title" style="top:2710px">OUR GALLERY</h2>
<div class="g-photo" role="img" aria-label="Lawn bordered by colourful flowering shrubs" style="left:98px;background:linear-gradient(180deg,#5e8a3a 0%,#4a7a2a 55%,#6fb035 100%)"></div>
<div class="g-photo g-follow" role="img" aria-label="Stone garden path lined with flowers" style="left:351px;width:241px;height:297px;top:2777px;background:linear-gradient(180deg,#3c4a34,#4c5a48 50%,#3a4a2a)">
  <span>Follow us on our socials</span>
  <span style="width:22px;height:22px;border-radius:50%;border:2px solid #fff"></span>
</div>
<div class="g-photo" role="img" aria-label="Wooden picket fence with purple lavender beds" style="left:611px;background:linear-gradient(180deg,#cdd6c0 0%,#b09a70 40%,#7a6aa8 75%,#4a7a2a 100%)"></div>
<div class="g-photo" role="img" aria-label="Misty garden with ornamental grasses and a garden arch" style="left:869px;background:linear-gradient(180deg,#6a6a3a 0%,#9a9a5a 50%,#5a5a30 100%)"></div>
<div class="abs btn-gold g-view">View More</div>

<section class="abs contact-section">
  <h2 class="section-title" style="top:82px">CONTACT US</h2>
</section>
<div class="c-field" style="left:182px;top:3415px;width:410px;height:48px">Name</div>
<div class="c-field" style="left:606px;top:3415px;width:411px;height:48px">Email</div>
<div class="c-field" style="left:182px;top:3478px;width:410px;height:48px">Phone Number</div>
<div class="c-field" style="left:606px;top:3478px;width:411px;height:48px">Subject</div>
<div class="c-field area" style="left:182px;top:3540px;width:835px;height:86px">Message</div>
<div class="abs btn-gold c-submit">Submit</div>

<footer class="abs footer">
  <div class="f-logo">
    <div class="logo-dot"></div>
    <div class="logo-name">BRIMSETT<br>GARDENING</div>
  </div>
  <span class="social" style="left:110px"></span>
  <span class="social" style="left:150px"></span>
  <span class="social" style="left:190px"></span>
  <span class="social" style="left:231px"></span>

  <div class="f-col" style="left:381px">
    <h4>Quick Links</h4>
    <ul>
      <li><svg width="14" height="12" viewBox="0 0 14 12"><path d="M0 5h9V1l5 5-5 5V7H0z" fill="#fff"/></svg>Home</li>
      <li><svg width="14" height="12" viewBox="0 0 14 12"><path d="M0 5h9V1l5 5-5 5V7H0z" fill="#fff"/></svg>Services</li>
      <li><svg width="14" height="12" viewBox="0 0 14 12"><path d="M0 5h9V1l5 5-5 5V7H0z" fill="#fff"/></svg>About Us</li>
      <li><svg width="14" height="12" viewBox="0 0 14 12"><path d="M0 5h9V1l5 5-5 5V7H0z" fill="#fff"/></svg>Gallery</li>
      <li><svg width="14" height="12" viewBox="0 0 14 12"><path d="M0 5h9V1l5 5-5 5V7H0z" fill="#fff"/></svg>Contact Us</li>
    </ul>
  </div>
  <div class="f-col" style="left:597px">
    <h4>Other Links</h4>
    <ul>
      <li><svg width="14" height="12" viewBox="0 0 14 12"><path d="M0 5h9V1l5 5-5 5V7H0z" fill="#fff"/></svg>FAQ</li>
      <li><svg width="14" height="12" viewBox="0 0 14 12"><path d="M0 5h9V1l5 5-5 5V7H0z" fill="#fff"/></svg>Terms of Use</li>
      <li><svg width="14" height="12" viewBox="0 0 14 12"><path d="M0 5h9V1l5 5-5 5V7H0z" fill="#fff"/></svg>Privacy Policy</li>
      <li><svg width="14" height="12" viewBox="0 0 14 12"><path d="M0 5h9V1l5 5-5 5V7H0z" fill="#fff"/></svg>Support Links</li>
      <li><svg width="14" height="12" viewBox="0 0 14 12"><path d="M0 5h9V1l5 5-5 5V7H0z" fill="#fff"/></svg>Conditions</li>
    </ul>
  </div>
  <div class="f-contact">
    <svg width="48" height="42" viewBox="0 0 48 42" fill="none" stroke="#e2b547" stroke-width="2.5"><rect x="14" y="4" width="30" height="20" rx="2"/><path d="M14 6l15 11 15-11"/><path d="M4 16c0 12 10 22 22 22l4-6-7-4-3 3c-4-2-7-5-9-9l3-3-4-7z" fill="#e2b547" stroke="none"/></svg>
    <h4>Contact Us</h4>
    <p style="top:63px">Phone:+1 555 014 0198</p>
    <p style="top:95px">Mail:info@brimsettgardening.com</p>
  </div>
  <div class="divider"></div>
  <p class="copyright">Copyrights@2023.Brimsett Gardening.All Rights Reserved</p>
</footer>

</body>
</html>
```